TLK Electricial Contracting Services

Hi guys, after a design for my small electrical company, have logo design files to be incorporated into the layout, the basic concept is electrical contracting services for residential, commercial, industrial & data services, image is clean clear and strong,

Card format is to have a nice clean logo on front,with maybe the Residential – commercial – industrial - data, followed with licensed & insured, followed by contact details on backside of the card.

Target Market(s)

Residential, commercial, industrial sectors.

Industry/Entity Type

Electrical

Contact Information for Business Card

TLK logo,
Residential – commercial – industrial - data
REC: 61307
Email: tlk@vornamail.net.au
Phone: 0487 352 019

Requirements
Must have
• Clean & strong design.
Nice to have
• If possible, I would like the logo colours inverted so the text is orange and the background is black on the front of the card, then the backside of the card be the reverse colour
Should not have
• No Sparks, lightning bolts,

```html
<!DOCTYPE html>
<html lang="en">
<head>
<meta charset="utf-8">
<title>TLK Electrical – Business Card</title>
<link rel="stylesheet" href="https://fonts.googleapis.com/css2?family=Alegreya:wght@400;600&display=swap">
<style>
  :root {
    --page-bg: #e9e6e1;
    --card-black: #050505;
    --accent-orange: #f0852d;
    --text-light: #f2f2f2;
    --card-shadow: rgba(0, 0, 0, 0.28);
  }
  * { margin: 0; padding: 0; box-sizing: border-box; }
  html, body {
    width: 1200px;
    height: 900px;
    overflow: hidden;
    background: var(--page-bg);
    font-family: "Alegreya", Georgia, serif;
  }
  .canvas {
    position: relative;
    width: 1200px;
    height: 900px;
  }
  .card {
    position: absolute;
    left: 290px;
    width: 620px;
    height: 354px;
    background: var(--card-black);
    box-shadow: 0 8px 22px var(--card-shadow);
  }
  .card--front { top: 70px; }
  .card--back  { top: 476px; }

  .brand {
    color: var(--accent-orange);
    font-weight: 600;
    text-align: center;
    line-height: 1;
  }
  .brand__mark {
    display: block;
    font-size: 64px;
    letter-spacing: 1px;
  }
  .brand__name {
    display: block;
    font-size: 13px;
    margin-top: 4px;
  }
  .card--front .brand {
    position: absolute;
    left: 0;
    right: 0;
    top: 128px;
  }
  .card--back .brand {
    position: absolute;
    right: 44px;
    top: 36px;
  }

  .holder {
    position: absolute;
    left: 58px;
    top: 170px;
  }
  .holder__name {
    color: var(--accent-orange);
    font-size: 27px;
    font-weight: 400;
    line-height: 1.1;
  }
  .holder__title {
    color: var(--text-light);
    font-size: 17px;
    line-height: 1.3;
  }

  .contact {
    position: absolute;
    left: 58px;
    top: 252px;
    color: var(--text-light);
    font-size: 15px;
    line-height: 1.55;
    list-style: none;
  }
  .contact__label { color: var(--accent-orange); }
  .contact__gap { margin-left: 14px; }
  .contact__web { color: var(--accent-orange); margin-left: 18px; }
</style>
</head>
<body>
<main class="canvas">
  <section class="card card--front" aria-label="Card front">
    <div class="brand">
      <span class="brand__mark">TLK</span>
      <span class="brand__name">Tobin Lake Electrical</span>
    </div>
  </section>

  <section class="card card--back" aria-label="Card back">
    <div class="brand">
      <span class="brand__mark">TLK</span>
      <span class="brand__name">Tobin Lake Electrical</span>
    </div>

    <div class="holder">
      <h1 class="holder__name">Daniel Hartley</h1>
      <p class="holder__title">Managing Director</p>
    </div>

    <ul class="contact">
      <li>1234, Address GoesHere, Country, 12345</li>
      <li>
        <span class="contact__label">T:</span> (044) 123 456 789
        <span class="contact__gap"><span class="contact__label">F:</span> (044) 123456789</span>
        <span class="contact__gap"><span class="contact__label">M:</span> (044)123456789</span>
      </li>
      <li>
        <span class="contact__label">E:</span> info@youremail.com
        <span class="contact__web">www.yourweb.com</span>
      </li>
    </ul>
  </section>
</main>
</body>
</html>
```